Business Cards - Brightpath Horizon

need to design unique business card for my mortgage business. I need to design credit card style business card for my business or any unique idea that you might have

Target Market(s)

Home Loan customers

Industry/Entity Type

Mortgage Brokerage

Contact Information for Business Card

please design credit card style or very unique style business card

Colors

Designer to choose colors to be used in the design.

Requirements
Must have
• Name
• position
• Phone number
• fax number
• email address
• website address
• social media address
• All above fields will be provided once design in finalised

```html
<!DOCTYPE html>
<html lang="en">
<head>
<meta charset="UTF-8">
<title>Brightpath Horizon – Business Card</title>
<link href="https://fonts.googleapis.com/css2?family=Libre+Baskerville:ital,wght@0,400;1,400&display=swap" rel="stylesheet">
<style>
  :root {
    --bg: #e9e6e1;
    --card-white: #ffffff;
    --brand-blue: #0530c4;
    --brand-orange: #ff8a12;
    --roof-orange: #ff8c10;
    --text-white: #ffffff;
    --shadow: rgba(0, 0, 0, 0.35);
  }
  * { margin: 0; padding: 0; box-sizing: border-box; }
  html, body { width: 1200px; height: 960px; overflow: hidden; }
  body {
    background: var(--bg);
    position: relative;
    font-family: "Libre Baskerville", Georgia, serif;
  }
  .card {
    position: absolute;
    box-shadow: 2px 3px 6px var(--shadow);
    overflow: hidden;
  }
  /* Front */
  .card-front {
    left: 314px; top: 113px; width: 600px; height: 343px;
    background: var(--card-white);
  }
  .brand-front {
    position: absolute; left: 34px; top: 50px;
    color: var(--brand-blue);
    font-size: 34px; line-height: 40px;
    font-weight: 400;
    white-space: nowrap;
  }
  .tagline {
    position: absolute;
    font-style: italic;
    font-size: 13px;
    white-space: nowrap;
  }
  .tagline-front { left: 64px; top: 138px; color: var(--brand-orange); }
  .person { position: absolute; right: 38px; top: 44px; text-align: right; }
  .person-name { color: var(--brand-blue); font-size: 19px; letter-spacing: 0.5px; white-space: nowrap; }
  .person-role { color: var(--brand-orange); font-size: 14px; margin-top: 4px; }
  .contact-band {
    position: absolute; left: 0; top: 185px; width: 600px; height: 135px;
    background: var(--brand-blue);
  }
  .contact-list {
    position: absolute; left: 33px; top: 32px;
    list-style: none; color: var(--text-white); font-size: 13px;
  }
  .contact-list li { display: flex; align-items: center; height: 19.5px; white-space: nowrap; }
  .contact-list svg { width: 13px; height: 13px; margin-right: 9px; fill: var(--text-white); flex: none; }
  .roof-art {
    position: absolute; left: 275px; top: 185px; width: 325px; height: 135px;
    background: linear-gradient(160deg, var(--brand-blue) 0%, var(--brand-blue) 30%, #ffffff 55%, var(--roof-orange) 100%);
  }
  /* Back */
  .card-back {
    left: 311px; top: 472px; width: 600px; height: 342px;
    background: var(--brand-orange);
  }
  .brand-back {
    position: absolute; left: 0; width: 600px; top: 118px;
    text-align: center; color: var(--text-white);
    font-size: 38px; line-height: 44px;
  }
  .tagline-back { left: 0; width: 600px; text-align: center; top: 226px; color: var(--text-white); font-size: 14px; }
  .social-row {
    position: absolute; left: 242px; top: 281px;
    display: flex; gap: 4px;
  }
  .social-dot { width: 26px; height: 26px; border-radius: 50%; background: var(--text-white); }
</style>
</head>
<body>

<section class="card card-front">
  <div class="brand-front">Brightpath<br>Horizon</div>
  <p class="tagline tagline-front">Clear choice, Solid ground</p>

  <div class="person">
    <p class="person-name">DANIEL REYES</p>
    <p class="person-role">CEO/FOUNDER</p>
  </div>

  <div class="contact-band">
    <ul class="contact-list">
      <li>
        <svg viewBox="0 0 16 16"><path d="M3.6 1l2.4 2.6-1.3 2c.9 2 2.5 3.6 4.6 4.6l2-1.3L14 11.4 12.6 14C6.8 13.7 2.3 9.2 2 3.4z"/></svg>
        614 552 3087
      </li>
      <li>
        <svg viewBox="0 0 16 16"><rect x="4" y="1" width="8" height="4"/><rect x="1" y="6" width="14" height="6" rx="1"/><rect x="4" y="10" width="8" height="5"/></svg>
        614 552 3090
      </li>
      <li>
        <svg viewBox="0 0 16 16"><path d="M1 3h14v10H1z M2 4l6 5 6-5" fill="none" stroke="#fff" stroke-width="1.5"/></svg>
        hello@brightpath.co
      </li>
      <li>
        <svg viewBox="0 0 16 16"><circle cx="8" cy="8" r="7"/><path d="M1 8h14M8 1c-3 3-3 11 0 14M8 1c3 3 3 11 0 14" fill="none" stroke="#0530c4" stroke-width="1"/></svg>
        www.brightpath.co
      </li>
    </ul>
  </div>
  <div class="roof-art" role="img" aria-label="Illustration of house rooftops with windows in blue and orange"></div>
</section>

<section class="card card-back">
  <div class="brand-back">Brightpath<br>Horizon</div>
  <p class="tagline tagline-back">Clear choice, Solid ground</p>
  <div class="social-row" aria-label="Social media links">
    <span class="social-dot"></span>
    <span class="social-dot"></span>
    <span class="social-dot"></span>
    <span class="social-dot"></span>
  </div>
</section>

</body>
</html>
```